Sparrow Haulage needs a business card design.

Design a double-sided business card for new freight business. On the front, would like to see our logo along with the following info:

Martin Obuya
CEO/FOUNDER
555-206-7142
martinobuya@sparrow-haulage.example

On the reverse side, we would like to use the graphic image of our logo only without the Sparrow Haulage name.

```html
<!DOCTYPE html>
<html lang="en">
<head>
<meta charset="utf-8">
<title>Sparrow Haulage — Business Card</title>
<link rel="stylesheet" href="https://fonts.googleapis.com/css2?family=Lato:wght@400;700;900&display=swap">
<style>
  :root {
    --navy: #1b1757;
    --red: #b8202a;
    --ink: #222222;
    --paper: #ffffff;
    --stage: #2a2a2c;
    --rule: #555555;
  }
  * { margin: 0; padding: 0; box-sizing: border-box; }
  html, body {
    width: 1200px;
    height: 900px;
    overflow: hidden;
    background: var(--stage);
    font-family: "Lato", sans-serif;
  }
  .sheet {
    width: 1200px;
    height: 900px;
    display: flex;
    flex-direction: column;
    align-items: center;
    justify-content: center;
    gap: 40px;
  }
  .card {
    width: 680px;
    height: 388px;
    position: relative;
    box-shadow: 0 10px 28px rgba(0,0,0,0.45);
  }

  /* Reverse side: brand graphic only */
  .card--back {
    background: var(--navy);
    display: flex;
    align-items: center;
    justify-content: center;
  }
  .back-mark {
    width: 64px;
    height: 64px;
    background: var(--paper);
  }

  /* Front side */
  .card--front {
    background: var(--paper);
    display: flex;
    align-items: center;
  }
  .brand {
    display: flex;
    align-items: center;
    gap: 14px;
    margin-left: 52px;
    width: 250px;
    color: var(--navy);
    font-size: 22px;
    font-weight: 900;
    text-transform: uppercase;
    letter-spacing: 0.12em;
    line-height: 1.05;
  }
  .brand__mark {
    width: 22px;
    height: 22px;
    flex: none;
    background: var(--red);
  }
  .brand__name span { display: block; }
  .divider {
    width: 1px;
    height: 104px;
    background: var(--rule);
    margin: 0 28px 0 18px;
  }
  .contact { color: var(--ink); }
  .contact__name {
    font-size: 24px;
    font-weight: 700;
    color: var(--navy);
    line-height: 1.1;
  }
  .contact__name .surname { color: var(--red); }
  .contact__role {
    font-size: 16px;
    letter-spacing: 0.02em;
    margin: 4px 0 12px;
  }
  .contact__line {
    display: flex;
    align-items: center;
    gap: 9px;
    font-size: 15px;
    line-height: 1.6;
    white-space: nowrap;
  }
  .contact__icon { width: 13px; height: 13px; flex: none; }
</style>
</head>
<body>
  <main class="sheet">
    <section class="card card--back" aria-label="Card reverse side">
      <div class="back-mark" role="img" aria-label="Sparrow Haulage brand graphic"></div>
    </section>

    <section class="card card--front" aria-label="Card front side">
      <div class="brand">
        <span class="brand__mark"></span>
        <span class="brand__name"><span>Sparrow</span><span>Haulage</span></span>
      </div>
      <div class="divider"></div>
      <div class="contact">
        <p class="contact__name">Martin <span class="surname">Obuya</span></p>
        <p class="contact__role">CEO/FOUNDER</p>
        <p class="contact__line">
          <svg class="contact__icon" viewBox="0 0 24 24" aria-hidden="true">
            <path fill="#b8202a" d="M6.6 10.8a15.1 15.1 0 0 0 6.6 6.6l2.2-2.2a1 1 0 0 1 1-.25 11.4 11.4 0 0 0 3.6.57 1 1 0 0 1 1 1V20a1 1 0 0 1-1 1A17 17 0 0 1 3 4a1 1 0 0 1 1-1h3.5a1 1 0 0 1 1 1c0 1.25.2 2.45.57 3.57a1 1 0 0 1-.25 1z"/>
          </svg>
          555-206-7142
        </p>
        <p class="contact__line">
          <svg class="contact__icon" viewBox="0 0 24 24" aria-hidden="true">
            <path fill="#b8202a" d="M2 5h20v14H2z"/>
            <path fill="none" stroke="#ffffff" stroke-width="2" d="M2 6l10 7 10-7"/>
          </svg>
          martinobuya@sparrow-haulage.example
        </p>
      </div>
    </section>
  </main>
</body>
</html>
```